Corvane Paintless Dent Removal

Our company works on vehicles removing dents using a highly skilled trade which the metal is massaged out with special tools without disturbing the original paint, hence paintless dent removal. Besides keeping the paint and metal original its also very environmentally friendly since no paint or toxic fillers are used. Also we we are one of the most experienced companies in the business with 25 years

Target Market(s)

Retail Automobile consumers, Auto Dealerships and Auto Body Shops

Industry/Entity Type

Auto Repair

Contact Information for Business Card

Dale Hollister
PO Box 518 Brookmere, NY 11962
631-555-0148
corvanepdr@mailbox-example.com
website corvanepdr.example
youtube corvane paintless dent removal
25 years of experience removing Dents, Dings and Hail Damage

Font styles to use
Serif
Sans Serif

Colors

Designer to choose colors to be used in the design.

Requirements
Must have
• I do like things that are simple but classy and somewhat bold, also I like my logo so that should be somewhat important

```html
<!DOCTYPE html>
<html lang="en">
<head>
<meta charset="utf-8">
<title>Corvane Paintless Dent Removal — Business Card</title>
<link rel="stylesheet" href="https://fonts.googleapis.com/css2?family=Roboto:wght@400;700;900&display=swap">
<style>
  :root {
    --backdrop: #3b3b3d;
    --card: #262628;
    --green: #7cc422;
    --blue: #0d4c97;
    --text: #f1f1f1;
    --muted: #d4d4d4;
  }
  html, body {
    margin: 0;
    width: 799px;
    height: 1200px;
    overflow: hidden;
    background: var(--backdrop);
    font-family: "Roboto", Arial, sans-serif;
  }
  .canvas {
    position: relative;
    width: 799px;
    height: 1200px;
  }
  .card {
    position: absolute;
    left: 90px;
    width: 620px;
    height: 354px;
    background: var(--card);
    border-radius: 4px;
    box-shadow: 0 10px 30px rgba(0,0,0,.45);
    overflow: hidden;
  }
  .card--front { top: 110px; }
  .card--back  { top: 700px; }

  .brand-name {
    margin: 0;
    font-weight: 900;
    color: var(--green);
    line-height: 1.05;
    text-transform: uppercase;
  }
  .card--front .brand {
    position: absolute;
    inset: 0;
    display: flex;
    align-items: center;
    justify-content: center;
    gap: 18px;
  }
  .brand-dot {
    width: 34px;
    height: 34px;
    border-radius: 50%;
    background: var(--blue);
    flex: none;
  }
  .card--front .brand-name { font-size: 40px; }
  .card--front .brand-name small {
    display: block;
    font-size: 18px;
    letter-spacing: .06em;
  }

  .card--back .brand {
    position: absolute;
    right: 34px;
    top: 48px;
    display: flex;
    align-items: center;
    gap: 12px;
  }
  .card--back .brand-dot { width: 22px; height: 22px; }
  .card--back .brand-name { font-size: 26px; }
  .card--back .brand-name small {
    display: block;
    font-size: 11.5px;
    letter-spacing: .06em;
  }

  .person {
    position: absolute;
    left: 34px;
    top: 60px;
  }
  .person-name {
    margin: 0;
    font-size: 26px;
    font-weight: 700;
    color: var(--green);
  }
  .person-role {
    margin: 2px 0 0;
    font-size: 13px;
    color: var(--muted);
  }
  .contact-list {
    list-style: none;
    margin: 18px 0 0;
    padding: 0;
    font-size: 14px;
    color: var(--text);
  }
  .contact-list li {
    display: flex;
    align-items: center;
    gap: 10px;
    margin-bottom: 6px;
  }
  .contact-list svg { width: 13px; height: 13px; fill: var(--green); flex: none; }

  .divider {
    position: absolute;
    left: 250px;
    right: 34px;
    top: 190px;
    height: 1.5px;
    background: var(--green);
  }
  .address {
    position: absolute;
    right: 34px;
    bottom: 30px;
    text-align: right;
    color: var(--text);
    font-size: 15px;
    line-height: 1.35;
  }
  .address p { margin: 0; }
  .video-link {
    display: flex;
    align-items: center;
    justify-content: flex-end;
    gap: 8px;
    margin-top: 6px !important;
  }
  .video-mark {
    width: 12px;
    height: 12px;
    background: var(--green);
    border-radius: 2px;
  }
</style>
</head>
<body>
<main class="canvas">
  <section class="card card--front" aria-label="Card front">
    <div class="brand">
      <span class="brand-dot"></span>
      <p class="brand-name">Corvane<small>Paintless Dent Removal</small></p>
    </div>
  </section>

  <section class="card card--back" aria-label="Card back">
    <div class="person">
      <h1 class="person-name">Dale Hollister</h1>
      <p class="person-role">Managing Director</p>
      <ul class="contact-list">
        <li>
          <svg viewBox="0 0 16 16" aria-hidden="true"><path d="M3.5 1l3 3-2 2c1 2 3 4 5 5l2-2 3 3-2 3C7 14 2 9 1 3.5z"/></svg>
          631-555-0148
        </li>
        <li>
          <svg viewBox="0 0 16 16" aria-hidden="true"><path d="M1 3h14v10H1zM2 4.2v.6l6 4 6-4v-.6H2z"/></svg>
          corvanepdr@mailbox-example.com
        </li>
        <li>
          <svg viewBox="0 0 16 16" aria-hidden="true"><path d="M8 1a7 7 0 100 14A7 7 0 008 1zm0 1.5c.8 0 1.8 1.8 2 4.5H6c.2-2.7 1.2-4.5 2-4.5zM2.6 8.5h2.4c.1 1.7.5 3.2 1 4.2A5.5 5.5 0 012.6 8.5zm0-1A5.5 5.5 0 016 3.3c-.5 1-.9 2.5-1 4.2zm3.4 1h4c-.2 2.7-1.2 4.5-2 4.5s-1.8-1.8-2-4.5zm5 0h2.4A5.5 5.5 0 0110 12.7c.5-1 .9-2.5 1-4.2zm0-1c-.1-1.7-.5-3.2-1-4.2a5.5 5.5 0 013.4 4.2z"/></svg>
          www.corvanepdr.example
        </li>
      </ul>
    </div>

    <div class="brand">
      <span class="brand-dot"></span>
      <p class="brand-name">Corvane<small>Paintless Dent Removal</small></p>
    </div>

    <div class="divider"></div>

    <div class="address">
      <p>PO Box 518 Brookmere,</p>
      <p>NY 11962</p>
      <p class="video-link"><span class="video-mark"></span>videohub.example/DaleHollister</p>
    </div>
  </section>
</main>
</body>
</html>
```